Oil Field Service company needs professional business cards

Looking to clean up our current company business cards and look a little more professional. Brenwick Casing Services is a US based company that services the oil field. We deal with engineers, managers and oil rigs....................................................................................................................................................................................................................................................................................................................................................................................................

Target Market(s)

Oil and Gas professionals

Industry/Entity Type

Oil And Gas

Contact Information for Business Card

See attached photo as example

Font styles to use
Sans Serif

Colors
ec1f27

Requirements
Must have
• Company Logo, Name, Title, Cell, Office, Fax, Email.
• See attached photo
Nice to have
• External CRT, Internal CRT, Casing Crews, Torque Turn, Laydown Machine
Should not have
• Do not introduce any new pictures and keep it professional looking

```html
<!DOCTYPE html>
<html lang="en">
<head>
<meta charset="utf-8">
<title>Brenwick Casing Services – Business Card</title>
<link href="https://fonts.googleapis.com/css2?family=Open+Sans:wght@400;600;700&family=Oswald:wght@500&display=swap" rel="stylesheet">
<style>
  :root {
    --bg: #383838;
    --slate: #3e4b56;
    --slate-back: #3d4a55;
    --red: #ec1f27;
    --paper: #f7f7f7;
    --ink-light: #ffffff;
    --divider: rgba(255,255,255,0.35);
  }
  * { margin: 0; padding: 0; box-sizing: border-box; }
  html, body { width: 1200px; height: 750px; overflow: hidden; }
  body {
    background: var(--bg);
    font-family: "Open Sans", Arial, sans-serif;
    position: relative;
  }
  .card {
    position: absolute;
    top: 228px;
    width: 461px;
    height: 262px;
    overflow: hidden;
    box-shadow: 0 3px 8px rgba(0,0,0,0.45);
  }
  .card-front { left: 124px; background: var(--paper); }
  .card-back { left: 618px; background: var(--slate-back); }

  .decor-panel {
    position: absolute;
    left: 252px; top: 0;
    width: 209px; height: 100%;
    background: linear-gradient(160deg, #44525e 0%, var(--slate) 60%);
  }

  .brand-name {
    position: absolute;
    text-align: center;
    font-weight: 700;
    line-height: 1;
  }
  .card-front .brand-name { left: 20px; width: 220px; top: 52px; color: var(--slate); }
  .card-back .brand-name { left: 40px; width: 200px; top: 110px; color: var(--ink-light); }
  .brand-name .brand-word { display: block; font-size: 32px; letter-spacing: 0.5px; }
  .brand-name .brand-sub { display: block; font-size: 11px; letter-spacing: 2.6px; margin-top: 10px; }

  .contact {
    position: absolute;
    right: 23px;
    top: 92px;
    text-align: right;
    color: var(--ink-light);
  }
  .person-name {
    font-family: "Oswald", "Arial Narrow", sans-serif;
    font-weight: 500;
    font-size: 17px;
    color: var(--red);
    line-height: 1.1;
  }
  .person-title { font-weight: 700; font-size: 13px; line-height: 1.3; }
  .address { font-size: 12px; margin-top: 7px; margin-bottom: 5px; }
  .contact-list { list-style: none; }
  .contact-list li {
    font-size: 12px;
    line-height: 17.6px;
    display: flex;
    justify-content: flex-end;
    align-items: center;
    gap: 8px;
  }
  .contact-list li.mobile { font-weight: 700; }
  .contact-list svg { width: 11px; height: 11px; fill: var(--red); flex: none; }

  .divider {
    position: absolute;
    left: 259px; top: 92px;
    width: 1px; height: 96px;
    background: var(--divider);
  }
  .services {
    position: absolute;
    left: 282px; top: 92px;
    list-style: none;
    color: var(--ink-light);
    font-size: 13px;
    line-height: 19.4px;
  }
  .services li::before {
    content: "";
    display: inline-block;
    width: 5px; height: 5px;
    border-radius: 50%;
    background: var(--red);
    margin-right: 8px;
    vertical-align: middle;
    position: relative; top: -2px;
  }
</style>
</head>
<body>

<section class="card card-front">
  <div class="decor-panel" role="img" aria-label="Slate and red decorative wave behind the contact details"></div>

  <div class="brand-name">
    <span class="brand-word">BRENWICK</span>
    <span class="brand-sub">CASING SERVICES</span>
  </div>

  <div class="contact">
    <p class="person-name">CODY HARLAN</p>
    <p class="person-title">AREA MANAGER</p>
    <p class="address">Redfield, OK 73900</p>
    <ul class="contact-list">
      <li class="office">(555)214-6300
        <svg viewBox="0 0 24 24"><path d="M6.6 10.8a15 15 0 0 0 6.6 6.6l2.2-2.2c.3-.3.7-.4 1-.2 1.1.4 2.3.6 3.6.6.6 0 1 .4 1 1V20c0 .6-.4 1-1 1A17 17 0 0 1 3 4c0-.6.4-1 1-1h3.5c.6 0 1 .4 1 1 0 1.3.2 2.5.6 3.6.1.3 0 .7-.2 1z"/></svg>
      </li>
      <li class="mobile">(555)387-1942
        <svg viewBox="0 0 24 24"><path d="M7 1h10a2 2 0 0 1 2 2v18a2 2 0 0 1-2 2H7a2 2 0 0 1-2-2V3a2 2 0 0 1 2-2zm0 3v15h10V4z"/></svg>
      </li>
      <li class="fax">(555)214-6310
        <svg viewBox="0 0 24 24"><path d="M6 2h12v6H6zM3 9h18a2 2 0 0 1 2 2v7h-4v4H5v-4H1v-7a2 2 0 0 1 2-2zm4 8v3h10v-3z"/></svg>
      </li>
      <li class="email">cody@brenwick.com
        <svg viewBox="0 0 24 24"><path d="M2 5h20v14H2zm2 2v.5l8 5 8-5V7z"/></svg>
      </li>
      <li class="web">www.brenwick.com
        <svg viewBox="0 0 24 24"><path d="M12 2a10 10 0 1 0 0 20 10 10 0 0 0 0-20zm0 2c1 0 2.3 2.2 2.7 6H9.3C9.7 6.2 11 4 12 4zm-7.9 8h3.2c.1 1.5.3 2.9.7 4H5.3a8 8 0 0 1-1.2-4zm5.2 0h5.4c-.2 3.7-1.6 6-2.7 6s-2.5-2.3-2.7-6z"/></svg>
      </li>
    </ul>
  </div>
</section>

<section class="card card-back">
  <div class="brand-name">
    <span class="brand-word">BRENWICK</span>
    <span class="brand-sub">CASING SERVICES</span>
  </div>
  <div class="divider"></div>
  <ul class="services">
    <li>External CRT</li>
    <li>Internal CRT</li>
    <li>Casing Crews</li>
    <li>Torque Turn</li>
    <li>Laydown Machine</li>
  </ul>
</section>

</body>
</html>
```